Computer consultant business card

Bexil Software is a newly started computer consulting company. It's a small one-man company that provides mostly Vornix applications but also websites in collaboration with designers. I'm running this company on the side of full time university studies.

I want the final design to be clean and memorable. Be creative! :)

Some inspiration:
http://www.pixelmarta.com/design/48317
http://www.pixelmarta.com/design/2739164/business-card-design-by-frostlynk
http://www.pixelmarta.com/design/604281/business-card-design-by-koralind-vestrabanu

See attachment for my company logo.
Updates

I would like to thank everyone for submitting! I'll need a couple of days to review and ultimately select a design.

Target Market(s)

Non-technical entrepreneurs and small companies.

Industry/Entity Type

University

Requirements
Must have
• My company logo.
In any way, both colors from my logo.
First- and last name, e-mail and phone number.
Double-sided design.
Nice to have
• Something creative with the symbol in my logo

```html
<!DOCTYPE html>
<html lang="en">
<head>
<meta charset="UTF-8">
<title>Bexil Software – Business Card</title>
<link rel="stylesheet" href="https://fonts.googleapis.com/css2?family=Nunito:wght@400;700&family=Questrial&display=swap">
<style>
  :root {
    --stage: #e9e4dc;
    --ink: #333335;
    --brand-blue: #4472b8;
    --paper: #ffffff;
    --night: #050505;
    --slate-top: #2f3035;
    --slate-bottom: #4a5a80;
    --label: #1c1c1c;
  }
  * { box-sizing: border-box; margin: 0; padding: 0; }
  html, body { width: 1200px; height: 788px; overflow: hidden; }
  body { background: var(--stage); position: relative; font-family: "Questrial", sans-serif; }

  .side-label {
    position: absolute; width: 526px; text-align: center;
    font-family: "Questrial", sans-serif; font-size: 20px; color: var(--label);
  }
  .card {
    position: absolute; width: 526px; height: 300px; border-radius: 20px; overflow: hidden;
    box-shadow: 0 3px 8px rgba(0,0,0,.35);
  }
  .card--front { left: 53px; top: 74px; }
  .card--back-light { left: 622px; top: 74px; background: var(--paper); }
  .card--back-dark { left: 53px; top: 445px; background: var(--night); }
  .card--back-slate { left: 622px; top: 445px;
    background: radial-gradient(ellipse at 50% 110%, var(--slate-bottom) 0%, var(--slate-top) 80%); }

  .front-shapes { position: absolute; inset: 0; }

  .wordmark {
    position: absolute; display: flex; align-items: center; gap: 22px;
    font-family: "Nunito", sans-serif; font-weight: 700; letter-spacing: 1px; line-height: 1;
  }
  .wordmark__mark { display: block; border-radius: 12px; background: var(--brand-blue); }
  .wordmark--front { left: 146px; top: 76px; font-size: 58px; color: var(--ink); }
  .wordmark--front .wordmark__mark { width: 60px; height: 60px; }
  .wordmark--back { left: 104px; top: 92px; font-size: 84px; }
  .wordmark--back .wordmark__mark { width: 100px; height: 100px; border-radius: 18px; }
  .wordmark--on-light { color: var(--ink); }
  .wordmark--on-dark { color: var(--paper); }

  .holder { position: absolute; left: 0; width: 419px; top: 163px; text-align: center; }
  .holder__name { font-family: "Nunito", sans-serif; font-weight: 700; font-size: 18px; color: var(--ink); }
  .holder__role { font-size: 13px; color: var(--brand-blue); margin-top: 2px; }

  .contact { position: absolute; left: 46px; top: 244px; font-size: 14px; color: var(--ink); line-height: 22px; }
  .contact__row { display: flex; align-items: center; gap: 9px; }
  .contact__icon { width: 10px; height: 10px; }

  .web {
    position: absolute; left: 0; right: 0; bottom: 30px; text-align: center;
    font-size: 18px; letter-spacing: 4px;
  }
  .web--on-light { color: var(--ink); }
  .web--on-dark { color: var(--paper); }

  .texture { position: absolute; }
  .texture--top { left: 0; top: 0; width: 300px; height: 150px;
    background: radial-gradient(ellipse at 45% 30%, rgba(90,90,95,.55), rgba(0,0,0,0) 70%); }
  .texture--bottom { right: 60px; bottom: 0; width: 240px; height: 150px;
    background: radial-gradient(ellipse at 40% 60%, rgba(120,110,110,.5), rgba(0,0,0,0) 70%); }
</style>
</head>
<body>

  <p class="side-label" style="left:53px; top:34px;">Front</p>
  <p class="side-label" style="left:622px; top:34px;">Back - 1</p>
  <p class="side-label" style="left:53px; top:405px;">Back - 2</p>
  <p class="side-label" style="left:622px; top:405px;">Back - 3</p>

  <!-- Front -->
  <section class="card card--front">
    <svg class="front-shapes" viewBox="0 0 526 300" width="526" height="300" aria-hidden="true">
      <rect width="526" height="300" fill="var(--ink)"/>
      <path d="M300,0 H526 V300 H150 V160 H300 Z" fill="var(--brand-blue)"/>
      <path d="M247,0 H467 C440,20 425,38 417,46 C450,60 470,90 470,130 C470,170 440,190 400,200 C300,215 255,232 207,300 H0 V225 C40,220 65,200 65,170 V90 C65,40 110,10 160,5 C200,2 230,0 247,0 Z" fill="var(--paper)"/>
    </svg>
    <div class="wordmark wordmark--front"><span class="wordmark__mark"></span>bexil</div>
    <div class="holder">
      <p class="holder__name">First Name + Last Name</p>
      <p class="holder__role">Designation</p>
    </div>
    <div class="contact">
      <p class="contact__row">
        <svg class="contact__icon" viewBox="0 0 10 10" aria-hidden="true"><path d="M2,0 L4,2.5 L3,3.5 C3.5,5 5,6.5 6.5,7 L7.5,6 L10,8 L8.5,10 C4,9.5 0.5,6 0,1.5 Z" fill="var(--ink)"/></svg>
        +12 345 6789
      </p>
      <p class="contact__row">
        <svg class="contact__icon" viewBox="0 0 10 10" aria-hidden="true"><rect x="0" y="2" width="10" height="7" fill="var(--ink)"/><path d="M0,2 L5,6 L10,2" stroke="var(--paper)" stroke-width="1" fill="none"/></svg>
        info@website.com
      </p>
    </div>
  </section>

  <!-- Back 1 -->
  <section class="card card--back-light">
    <div class="wordmark wordmark--back wordmark--on-light"><span class="wordmark__mark"></span>bexil</div>
    <p class="web web--on-light">www.website.com</p>
  </section>

  <!-- Back 2 -->
  <section class="card card--back-dark">
    <div class="texture texture--top" role="img" aria-label="Perforated metal dot texture"></div>
    <div class="texture texture--bottom" role="img" aria-label="Perforated metal dot texture"></div>
    <div class="wordmark wordmark--back wordmark--on-dark"><span class="wordmark__mark"></span>bexil</div>
    <p class="web web--on-dark">www.website.com</p>
  </section>

  <!-- Back 3 -->
  <section class="card card--back-slate">
    <div class="wordmark wordmark--back wordmark--on-dark"><span class="wordmark__mark"></span>bexil</div>
    <p class="web web--on-dark">www.website.com</p>
  </section>

</body>
</html>
```